Square graphic for social media post

I want to create a 1080 x 1080px all-black image for the quote below that I can share on social media. I want the emphasis to be primarily on the quote, secondarily on the portrait, and third (smallest) on the logo. I want the background on the portrait to be edited so it's transparent and just shows the face of the person on a black background (no brick wall visible).

Graphic color: black
Text color: white
Content: "What we went through is going to make the greatest generation of hoteliers our industry has ever seen." << biggest text
Derek Holm << smaller text
President, Silverbrook Hotels << smaller text
[image of person - use whichever version looks better to you]
[Add Lodging Ledger logo - whichever looks better to you]

This image needs to be readable when sized down much smaller (400x400?) so want the text and portrait to take up most of the space.

I'd like the output both as PNG and original file (preferably Canva). Thanks!

Target Market(s)

Hotel managers

Industry/Entity Type

Hospitality

Font styles to use
Sans Serif

Colors

Designer to choose colors to be used in the design.

Requirements
Must have
• Needs to focus on the quote and the person quoted (the portrait)

```html
<!DOCTYPE html>
<html lang="en">
<head>
<meta charset="utf-8">
<title>Derek Holm quote – Lodging Ledger</title>
<link href="https://fonts.googleapis.com/css2?family=Jost:wght@400;500&display=swap" rel="stylesheet">
<style>
  :root {
    --bg: #000000;
    --ink: #ffffff;
    --ink-soft: #f2f2f2;
    --portrait-light: #3a3a3a;
    --portrait-mid: #1c1c1c;
  }
  * { margin: 0; padding: 0; box-sizing: border-box; }
  html, body {
    width: 1200px;
    height: 1200px;
    overflow: hidden;
    background: var(--bg);
  }
  .quote-card {
    position: relative;
    width: 1200px;
    height: 1200px;
    background: var(--bg);
    font-family: "Jost", "Futura", sans-serif;
    color: var(--ink);
    overflow: hidden;
  }
  .portrait {
    position: absolute;
    left: 150px;
    top: -40px;
    width: 900px;
    height: 1300px;
    border-radius: 45% 45% 0 0;
    background:
      radial-gradient(ellipse 34% 30% at 50% 36%, var(--portrait-light) 0%, var(--portrait-mid) 60%, transparent 100%),
      radial-gradient(ellipse 55% 45% at 50% 95%, #161616 0%, transparent 100%);
  }
  .brand {
    position: absolute;
    top: 108px;
    left: 0;
    width: 100%;
    display: flex;
    justify-content: center;
    align-items: center;
    gap: 12px;
  }
  .brand-dot {
    width: 10px;
    height: 10px;
    border-radius: 50%;
    background: var(--ink);
  }
  .brand-name {
    font-size: 20px;
    font-weight: 500;
    letter-spacing: 5px;
    text-transform: uppercase;
    color: var(--ink);
  }
  .quote {
    position: absolute;
    top: 438px;
    left: 0;
    width: 100%;
    text-align: center;
    font-size: 57px;
    font-weight: 500;
    line-height: 83px;
    color: var(--ink);
  }
  .attribution-name {
    position: absolute;
    top: 895px;
    left: 0;
    width: 100%;
    text-align: center;
    font-size: 44px;
    font-weight: 500;
  }
  .attribution-title {
    position: absolute;
    top: 975px;
    left: 0;
    width: 100%;
    text-align: center;
    font-size: 27px;
    font-weight: 500;
    color: var(--ink-soft);
  }
</style>
</head>
<body>
  <main class="quote-card">
    <div class="portrait" role="img" aria-label="Darkened black-and-white portrait of Derek Holm, head and shoulders, on a black background"></div>

    <div class="brand">
      <span class="brand-dot"></span>
      <span class="brand-name">Lodging Ledger</span>
    </div>

    <blockquote class="quote">
      "What we went through is<br>
      going to make the greatest<br>
      generation of hoteliers our<br>
      industry has ever seen."
    </blockquote>

    <p class="attribution-name">- Derek Holm -</p>
    <p class="attribution-title">President, Silverbrook Hotels</p>
  </main>
</body>
</html>
```